Spring Detox sale graphics for social media

You MUST read the Brief in the WORD document and follow the instructions there. I want to create 10 social media graphics (new Instagram size 4:5 (1080 x 1350 pixels) focusing on our Mother’s Day Spring Detox Sale graphics, using any of the pics attached. Use the attached pics, NO RANDOM STOCK PHOTOGRAPHY. For the color scheme of the graphics, they should all be complementary to the product colors or feel like Spring time.

Target Market(s)

primarily women

Requirements
Must have
• the photos and text attached

```html
<!DOCTYPE html>
<html lang="en">
<head>
<meta charset="utf-8">
<title>Mother's Day Spring Detox Sale – Social Set</title>
<link href="https://fonts.googleapis.com/css2?family=Antonio:wght@700&family=Archivo:wdth,wght@62..125,700..900&family=Montserrat:ital,wght@0,700;0,900;1,900&display=swap" rel="stylesheet">
<style>
  :root{
    --backdrop:#595959;
    --white:#ffffff;
    --forest:#1f4a36;
    --sage:#3f7d60;
    --mint:#4d8c72;
    --red:#e32b2b;
    --plum:#9a4580;
    --orchid:#a83a8a;
    --wine:#6b2150;
    --brown:#4a2a1a;
    --cocoa:#5a2e1c;
    --royal:#2b52c8;
    --navy:#283593;
    --ink:#1d1d1d;
    --blush:#f0b8dc;
  }
  *{margin:0;padding:0;box-sizing:border-box}
  html,body{width:1200px;height:3484px;overflow:hidden;background:var(--backdrop)}
  .canvas{position:relative;width:1200px;height:3484px;background:var(--backdrop)}
  .post{position:absolute;width:494px;height:617px;background:var(--white);overflow:hidden}
  .col-a{left:88px}.col-b{left:630px}
  .row-1{top:107px}.row-2{top:766px}.row-3{top:1425px}.row-4{top:2084px}.row-5{top:2742px}
  .abs{position:absolute;line-height:1;white-space:nowrap}
  .cond{font-family:"Antonio",sans-serif;font-weight:700;text-transform:uppercase;letter-spacing:-0.5px}
  .wide{font-family:"Archivo",sans-serif;font-weight:900;font-stretch:125%;text-transform:uppercase}
  .heavy{font-family:"Archivo",sans-serif;font-weight:900;font-stretch:100%;text-transform:uppercase}
  .geo{font-family:"Montserrat",sans-serif;font-weight:900}
  .center{left:0;right:0;text-align:center}
  .bottles{position:absolute;border-radius:6px;background:linear-gradient(90deg,#e9ecf4 0%,#f7f7fa 30%,#f3e6ee 55%,#e3efe9 75%,#e6e9f3 100%)}
  .photo{position:absolute;background:linear-gradient(160deg,#b48a6a 0%,#7a5238 45%,#3c2a22 100%)}
  .band{position:absolute;left:0;right:0;display:flex;align-items:center;justify-content:center;color:var(--white);white-space:nowrap;line-height:1}
  .pct{display:inline-flex;flex-direction:column;line-height:.9;vertical-align:top}
</style>
</head>
<body>
<main class="canvas">

  <!-- 1 -->
  <section class="post col-a row-1">
    <svg class="abs" style="left:0;top:26px" width="412" height="81" viewBox="0 0 412 81"><polygon points="0,0 385,0 412,81 0,81" fill="var(--forest)"/></svg>
    <div class="abs geo" style="left:34px;top:48px;font-size:34px;font-weight:700;color:var(--white)">MOTHER’S DAY</div>
    <div class="abs cond" style="left:22px;top:128px;font-size:74px;color:var(--forest);line-height:1.1">SPRING<br>DETOX</div>
    <div class="bottles" role="img" aria-label="Row of four supplement bottles" style="left:254px;top:143px;width:219px;height:91px"></div>
    <div class="abs cond" style="right:20px;top:238px;font-size:130px;color:var(--forest)">SALE</div>
    <div class="abs geo center" style="top:398px;font-size:88px;color:var(--red)">25% OFF</div>
    <div class="abs cond center" style="top:497px;font-size:86px;color:var(--forest)">EVERYTHING!</div>
  </section>

  <!-- 2 -->
  <section class="post col-b row-1">
    <div class="band wide" style="top:0;height:73px;background:var(--plum);font-size:60px">25% OFF</div>
    <div class="abs" style="left:14px;top:133px;width:465px;height:428px;border:2px dotted var(--plum)"></div>
    <div class="abs cond center" style="top:110px"><span style="background:var(--white);padding:0 10px;font-size:42px;color:var(--red)">MOTHER’S DAY</span></div>
    <div class="abs cond center" style="top:185px;font-size:146px;color:var(--plum)">SPRING</div>
    <div class="abs cond center" style="top:330px;font-size:170px;color:var(--plum)">DETOX</div>
    <div class="abs cond center" style="top:528px"><span style="background:var(--white);padding:0 10px;font-size:62px;color:var(--red)">SALE</span></div>
  </section>

  <!-- 3 -->
  <section class="post col-a row-2">
    <div class="abs cond center" style="top:30px;font-size:84px;color:var(--brown)">SPRING DETOX</div>
    <div class="abs cond center" style="top:128px;font-size:84px;color:var(--brown)">SALE!</div>
    <div class="photo" role="img" aria-label="Smiling woman in a white top presenting the supplement range on a kitchen counter" style="left:0;top:220px;width:241px;height:323px;border-radius:120px 120px 0 0"></div>
    <div class="abs" style="left:210px;top:303px;width:330px;height:142px;transform:rotate(-90deg);display:flex;align-items:center">
      <span class="cond" style="font-size:180px;color:var(--red);line-height:.8">25</span>
      <span class="pct cond" style="color:var(--red);margin-left:6px"><span style="font-size:76px">%</span><span style="font-size:50px">OFF</span></span>
    </div>
    <div class="band cond" style="top:543px;height:74px;background:var(--cocoa);font-size:58px">ALL SUPPLEMENTS</div>
  </section>

  <!-- 4 -->
  <section class="post col-b row-2">
    <div class="abs" style="left:58px;top:18px;display:flex;color:var(--ink)">
      <span class="wide" style="font-size:130px;line-height:.85">25</span>
      <span class="pct heavy" style="margin-left:4px"><span style="font-size:58px">%</span><span style="font-size:44px">OFF</span></span>
    </div>
    <div class="abs cond" style="left:54px;top:153px;font-size:46px;color:var(--sage)">SPRING DETOX SALE</div>
    <div class="abs cond" style="left:55px;top:222px;font-size:104px;color:var(--forest)">SPRING</div>
    <div class="abs cond" style="right:24px;top:344px;font-size:104px;color:var(--forest)">RESET</div>
    <div class="bottles" role="img" aria-label="Group of four supplement bottles" style="left:11px;top:405px;width:230px;height:135px"></div>
    <div class="band wide" style="top:543px;height:74px;background:var(--sage);font-size:42px;font-stretch:110%">SUMMER READY</div>
  </section>

  <!-- 5 -->
  <section class="post col-a row-3">
    <div class="abs" style="left:30px;top:20px;display:flex;color:var(--red)">
      <span class="cond" style="font-size:132px;line-height:.85">25</span>
      <span class="pct cond" style="margin-left:4px"><span style="font-size:60px">%</span><span style="font-size:46px">OFF</span></span>
    </div>
    <div class="bottles" role="img" aria-label="Row of four supplement bottles" style="left:250px;top:30px;width:217px;height:95px"></div>
    <div class="abs heavy center" style="top:170px;font-size:60px;color:var(--royal);font-stretch:105%">EVERYTHING</div>
    <svg class="abs" style="left:0;top:255px" width="494" height="93" viewBox="0 0 494 93"><polygon points="14,0 494,0 480,93 0,93" fill="var(--royal)"/></svg>
    <div class="abs cond center" style="top:262px;font-size:76px;color:var(--white)">MOTHER’S DAY</div>
    <div class="abs cond center" style="top:358px;font-size:100px;color:var(--navy)">SPRING</div>
    <div class="abs cond center" style="top:472px;font-size:98px;color:var(--navy)">DETOX SALE</div>
  </section>

  <!-- 6 -->
  <section class="post col-b row-3">
    <div class="abs cond center" style="top:36px;font-size:76px;color:var(--red)">MOTHER’S DAY</div>
    <div class="abs cond center" style="top:118px;font-size:112px;color:var(--ink)">SALE</div>
    <div class="bottles" role="img" aria-label="Group of four supplement bottles" style="left:5px;top:272px;width:250px;height:135px"></div>
    <div class="abs" style="left:266px;top:272px;display:flex;color:var(--red)">
      <span class="cond" style="font-size:128px;line-height:.9">25</span>
      <span class="pct cond" style="margin-left:4px"><span style="font-size:60px">%</span><span style="font-size:46px">OFF</span></span>
    </div>
    <div class="abs" style="left:35px;top:459px;width:425px;height:123px;background:var(--red);display:flex;align-items:center;justify-content:center;text-align:center">
      <span class="geo" style="font-style:italic;font-size:40px;line-height:1.15;color:var(--white)">FEEL AMAZING<br>AGAIN!</span>
    </div>
  </section>

  <!-- 7 -->
  <section class="post col-a row-4">
    <div class="abs heavy" style="left:26px;top:22px;font-size:62px;font-stretch:95%;line-height:1.3;color:var(--orchid)">REFRESH<br>YOUR<br>BODY</div>
    <div class="photo" role="img" aria-label="Smiling woman in a white top with the supplement range in front of her" style="left:234px;top:135px;width:260px;height:250px;border-radius:125px 0 0 125px"></div>
    <div class="abs" style="left:0;top:425px;width:194px;height:8px;background:var(--blush)"></div>
    <div class="abs heavy" style="right:45px;top:402px;font-size:46px;font-stretch:90%;color:var(--red)">25% OFF</div>
    <div class="abs heavy" style="right:45px;top:464px;font-size:46px;font-stretch:90%;color:var(--orchid)">MOTHER’S DAY</div>
    <div class="abs heavy" style="right:45px;top:528px;font-size:46px;font-stretch:90%;color:var(--orchid)">SALE</div>
  </section>

  <!-- 8 -->
  <section class="post col-b row-4">
    <div class="band wide" style="top:0;height:72px;background:var(--forest);font-size:58px">25% OFF</div>
    <div class="abs cond center" style="top:84px;font-size:56px;color:var(--forest)">SPRING DETOX SALE</div>
    <div class="bottles" role="img" aria-label="Four supplement bottles in a row" style="left:62px;top:160px;width:376px;height:144px"></div>
    <div class="abs heavy center" style="top:312px;font-size:88px;font-stretch:105%;color:var(--forest)">SPRING</div>
    <div class="abs heavy center" style="top:408px;font-size:76px;font-stretch:105%;color:var(--mint)">CLEANSE</div>
    <div class="band cond" style="top:496px;height:121px;background:var(--forest);font-size:80px">SUMMER GLOW</div>
  </section>

  <!-- 9 -->
  <section class="post col-a row-5">
    <div class="abs" style="left:36px;top:40px;display:flex;color:var(--red)">
      <span class="cond" style="font-size:92px;line-height:.9">25</span>
      <span class="pct cond" style="margin-left:3px"><span style="font-size:44px">%</span><span style="font-size:32px">OFF</span></span>
    </div>
    <div class="bottles" role="img" aria-label="Group of four supplement bottles" style="left:189px;top:4px;width:278px;height:129px"></div>
    <svg class="abs" style="left:20px;top:142px" width="460" height="72" viewBox="0 0 460 72"><polygon points="20,0 460,0 440,72 0,72" fill="var(--wine)"/></svg>
    <div class="abs cond center" style="top:154px;font-size:46px;color:var(--white)">MOTHER’S DAY SALE</div>
    <div class="abs cond center" style="top:232px;color:var(--orchid)"><span style="font-size:110px">DETOX</span> <span style="font-size:46px">THIS</span></div>
    <div class="abs cond center" style="top:356px;font-size:110px;color:var(--orchid)">SPRING</div>
    <div class="band cond" style="top:482px;height:135px;background:var(--wine);gap:14px">
      <span style="font-size:96px">SHINE</span>
      <span style="font-size:42px;line-height:1;text-align:center">THIS<br>SUMMER</span>
    </div>
  </section>

  <!-- 10 -->
  <section class="post col-b row-5">
    <div class="abs cond center" style="top:18px;font-size:130px;color:var(--red)">25%OFF</div>
    <div class="abs cond center" style="top:152px;font-size:56px;color:var(--forest)">MOTHER’S DAY SALE</div>
    <div class="bottles" role="img" aria-label="Four supplement bottles in a row" style="left:57px;top:240px;width:389px;height:156px"></div>
    <div class="abs" style="left:20px;top:417px;width:445px;height:104px;background:var(--forest);display:flex;align-items:center;justify-content:center">
      <span class="cond" style="font-size:76px;line-height:1;color:var(--white)">SPRING DETOX</span>
    </div>
    <div class="abs cond center" style="top:534px;font-size:52px;color:var(--forest)">FOR A SUMMER BODY</div>
  </section>

</main>
</body>
</html>
```